Stylish Business Cards Wanted

- DOUBLE SIDED Design Required -

High end, edgy cards for a corporate and personal stylist. Must include logo,
Name: Belinda Harwick
Title: Director and Stylist
telephone : +61 8 7142 5809
email: belinda@theloombriefing.example
website: theloombriefing.example
Tag: Corporate Workwear & Uniform Specialist | Personal Stylist
Would like nice icons for telephone, email, website

Target Market(s)

Businesses wanting stylish uniforms, people wanting stylish wardrobes

Industry/Entity Type

Corporate Workwear Stylist

Contact Information for Business Card

I would like black, white and gold foiling incorporated in the design - possibly a touch of the other colours on my branding guide attached Name: Belinda Harwick Title: Director and Stylist telephone : +61 8 7142 5809 email: belinda@theloombriefing.example website: theloombriefing.example Tag: Corporate Workwear & Uniform Specialist | Personal Stylist Would like nice icons for telephone, email, website

Font styles to use
Other font styles liked:
• Raleway

Colors

Designer to choose colors to be used in the design.

Requirements
Must have
• Gold foil accents

```html
<!DOCTYPE html>
<html lang="en">
<head>
<meta charset="utf-8">
<title>The Loom Briefing – Business Cards</title>
<link rel="stylesheet" href="https://fonts.googleapis.com/css2?family=Cinzel:wght@700&family=Open+Sans:wght@400;600&display=swap">
<style>
  :root {
    --paper: #ffffff;
    --ink: #333233;
    --gold: #e4bd5c;
    --backdrop: #ebe7e1;
    --text-light: #ffffff;
  }
  * { box-sizing: border-box; margin: 0; padding: 0; }
  html, body {
    width: 1200px;
    height: 920px;
    overflow: hidden;
    background: var(--backdrop);
  }
  .sheet {
    position: relative;
    width: 1200px;
    height: 920px;
  }
  .card {
    position: absolute;
    left: 250px;
    width: 700px;
    height: 400px;
    background: var(--paper);
    overflow: hidden;
    box-shadow: 0 8px 24px rgba(0,0,0,0.12);
  }
  .card--back { top: 40px; }
  .card--front { top: 480px; }
  .card__wave {
    position: absolute;
    inset: 0;
    width: 100%;
    height: 100%;
  }
  .wave-dark { fill: var(--ink); }
  .wave-gold { fill: var(--gold); }

  .brand {
    position: absolute;
    display: flex;
    align-items: center;
    gap: 12px;
    font-family: "Open Sans", sans-serif;
    font-weight: 600;
    font-size: 30px;
    letter-spacing: 1px;
    color: var(--ink);
    white-space: nowrap;
  }
  .brand__mark {
    width: 16px;
    height: 16px;
    background: var(--gold);
    flex: none;
  }
  .card--back .brand {
    top: 120px;
    left: 50%;
    transform: translateX(-50%);
  }
  .card--front .brand {
    top: 110px;
    left: 48px;
  }

  .identity {
    position: absolute;
    top: 92px;
    right: 48px;
    text-align: left;
  }
  .identity__name {
    font-family: "Cinzel", serif;
    font-weight: 700;
    font-size: 27px;
    letter-spacing: 0.5px;
    color: var(--ink);
    line-height: 1;
    white-space: nowrap;
  }
  .identity__title {
    font-family: "Open Sans", sans-serif;
    font-size: 14px;
    color: var(--ink);
    margin-top: 2px;
  }

  .contacts {
    position: absolute;
    right: 38px;
    bottom: 20px;
    list-style: none;
  }
  .contacts__item {
    display: flex;
    justify-content: flex-end;
    align-items: center;
    gap: 14px;
    font-family: "Open Sans", sans-serif;
    font-size: 15px;
    color: var(--text-light);
    line-height: 1;
    height: 26px;
    white-space: nowrap;
  }
  .contacts__icon {
    width: 17px;
    height: 17px;
    flex: none;
    fill: none;
    stroke: var(--text-light);
    stroke-width: 1.6;
  }
</style>
</head>
<body>
<main class="sheet">

  <section class="card card--back" aria-label="Card back">
    <svg class="card__wave" viewBox="0 0 700 400" preserveAspectRatio="none" aria-hidden="true">
      <path class="wave-gold" d="M0,262 C130,210 300,195 440,205 C540,212 630,235 700,265 L700,278 C620,248 530,228 430,222 C300,215 140,230 0,282 Z"/>
      <path class="wave-dark" d="M0,300 C140,250 300,232 440,240 C550,246 630,268 700,298 L700,400 L0,400 Z"/>
    </svg>
    <div class="brand"><span class="brand__mark"></span>The Loom Briefing</div>
  </section>

  <section class="card card--front" aria-label="Card front">
    <svg class="card__wave" viewBox="0 0 700 400" preserveAspectRatio="none" aria-hidden="true">
      <path class="wave-gold" d="M0,328 C110,362 250,352 390,300 C260,368 110,382 0,350 Z"/>
      <path class="wave-gold" d="M430,250 C530,205 630,210 700,262 L700,282 C630,232 540,222 460,256 Z"/>
      <path class="wave-dark" d="M0,372 C160,378 330,335 470,275 C560,238 640,245 700,292 L700,400 L0,400 Z"/>
    </svg>

    <div class="brand"><span class="brand__mark"></span>The Loom Briefing</div>

    <div class="identity">
      <h1 class="identity__name">Belinda Harwick</h1>
      <p class="identity__title">Director and Stylist</p>
    </div>

    <ul class="contacts">
      <li class="contacts__item">+61 8 7142 5809
        <svg class="contacts__icon" viewBox="0 0 24 24" aria-hidden="true"><path d="M5 3h4l2 5-2.5 1.5a11 11 0 0 0 6 6L16 13l5 2v4a2 2 0 0 1-2 2A16 16 0 0 1 3 5a2 2 0 0 1 2-2z"/></svg>
      </li>
      <li class="contacts__item">+61 4 1200 5809
        <svg class="contacts__icon" viewBox="0 0 24 24" aria-hidden="true"><rect x="6" y="2" width="12" height="20" rx="2"/><line x1="11" y1="18.5" x2="13" y2="18.5"/></svg>
      </li>
      <li class="contacts__item">belinda@theloombriefing.example
        <svg class="contacts__icon" viewBox="0 0 24 24" aria-hidden="true"><rect x="2" y="5" width="20" height="14"/><path d="M2 5l10 8 10-8"/></svg>
      </li>
      <li class="contacts__item">theloombriefing.example
        <svg class="contacts__icon" viewBox="0 0 24 24" aria-hidden="true"><circle cx="12" cy="12" r="9.5"/><ellipse cx="12" cy="12" rx="4" ry="9.5"/><line x1="2.5" y1="12" x2="21.5" y2="12"/><line x1="4" y1="7" x2="20" y2="7"/><line x1="4" y1="17" x2="20" y2="17"/></svg>
      </li>
    </ul>
  </section>

</main>
</body>
</html>
```